Export company based in South America (Ecuador) we export flowers, chocolate, and bananas

We need a website that gives our potential clients and introduction into our company and the different types of commodities we export around the world. We are based in Quito, Ecuador so the website should portray the feel of Ecuadorian landscapes within a modern looking website.
At the moment we are exporting roses, chocolate, and bananas so the website should have an intro to our company and then three different areas that describe our three main commodity. The three different sections should explain why each of the products from Ecuador are some of the best in the world in their categories and the benefits of importing the commodity through our company.
Industry/Entity Type
Commodity
Number of Pages Required
4 page

```html
<!DOCTYPE html>
<html lang="en">
<head>
<meta charset="utf-8">
<title>Verdano — Ecuadorian Exports</title>
<link rel="stylesheet" href="https://fonts.googleapis.com/css2?family=Montserrat:wght@400;500;600;700&family=Open+Sans:wght@400;600&display=swap">
<style>
:root{
  --orange:#f7941d;
  --orange-light:#fbab3d;
  --ink:#1f1f1f;
  --text:#555555;
  --dark:#262c37;
  --footer:#1e1e1e;
  --white:#ffffff;
  --grey-bg:#e4e4e4;
}
*{margin:0;padding:0;box-sizing:border-box}
html,body{width:1200px;height:3476px;overflow:hidden}
body{position:relative;background:var(--white);font-family:"Open Sans",Arial,sans-serif;color:var(--text)}
.abs{position:absolute}
.heading{font-family:"Montserrat",Arial,sans-serif;font-weight:600;color:var(--ink);text-transform:uppercase}
.btn{position:absolute;display:flex;align-items:center;justify-content:center;background:var(--orange);color:#2a1a05;font-family:"Montserrat",Arial,sans-serif;font-weight:600;font-size:14px;text-transform:uppercase}
.btn.inline{position:static;flex:none}
.text-block{position:absolute;display:flex;flex-direction:column;align-items:flex-start}
.body-copy{font-size:12.4px;line-height:27px}
.diag{position:absolute;left:0;width:1200px;display:block}

/* hero */
.hero{position:absolute;left:0;top:0;width:1200px;height:645px;overflow:hidden}
.hero-photo{position:absolute;inset:0;background:linear-gradient(180deg,#7d8ea6 0%,#9aa6b6 28%,#6f7a6a 45%,#3d5230 62%,#4a5a6e 75%,#2e3d22 100%)}
.logo{position:absolute;left:144px;top:18px;font-family:"Montserrat",Arial,sans-serif;font-weight:600;font-size:40px;color:var(--white)}
.nav{position:absolute;top:32px;left:373px;display:flex;gap:33px;font-family:"Montserrat",Arial,sans-serif;font-size:13px;color:var(--white)}
.nav .active{color:var(--orange)}
.nav-search{position:absolute;left:826px;top:33px}
.nav-btn{position:absolute;top:25px;height:30px;border:1px solid var(--white);color:var(--white);font-family:"Montserrat",Arial,sans-serif;font-size:13px;display:flex;align-items:center;justify-content:center}
.hero-title{position:absolute;top:238px;left:0;width:1200px;text-align:center;font-size:34px;line-height:40px;color:#1d1d1d}
.slider-arrow{position:absolute;top:304px;width:40px;height:40px;background:#111;display:flex;align-items:center;justify-content:center}

/* welcome */
.welcome-title{left:144px;top:728px;font-size:32px}
.welcome-block{left:144px;top:782px;width:462px}
.accent-line{position:absolute;height:3px;background:var(--orange)}
.photo-block{position:absolute}

/* products */
.products{position:absolute;left:0;top:1095px;width:1200px;height:667px;background:linear-gradient(180deg,#2a3140 0%,#2c3442 55%,#3a3f48 80%,#333a45 100%)}
.products-title{position:absolute;top:1168px;left:0;width:1200px;text-align:center;font-size:32px;color:var(--white)}
.product-card{position:absolute;width:297px;height:336px;background:var(--white);text-align:center}
.product-card h3{margin-top:78px;font-size:24px}
.product-card p{margin:6px auto 0;width:250px;font-size:10.5px;line-height:17px;color:#555}
.product-card .product-photo{position:absolute;left:8px;bottom:8px;width:281px;height:144px}
.card-stem{position:absolute;width:3px;height:118px;background:var(--orange)}

/* why */
.why-title{left:628px;top:1845px;font-size:32px}
.why-block{left:628px;top:1900px;width:432px}

/* benefits */
.benefits{position:absolute;left:0;top:2214px;width:1200px;height:709px;background:linear-gradient(180deg,#ececec,#dcdcdc 50%,#e8e8e8)}
.benefit-circle{position:absolute;width:160px;height:160px;border-radius:50%;background:var(--orange);display:flex;align-items:center;justify-content:center}
.benefit-label{position:absolute;font-family:"Montserrat",Arial,sans-serif;font-size:24px;line-height:35px;color:#1e1e1e}
.benefits-title{position:absolute;top:2534px;left:0;width:1200px;text-align:center;font-size:32px}

/* contact */
.contact-title{position:absolute;top:2996px;left:0;width:1200px;text-align:center;font-size:32px}
.contact-line{position:absolute;left:0;width:1200px;text-align:center;font-family:"Montserrat",Arial,sans-serif;font-size:23px;color:#1e1e1e}
.contact-line svg{vertical-align:-2px;margin-right:6px}

/* footer */
.footer{position:absolute;left:0;top:3294px;width:1200px;height:182px;background:var(--footer)}
.footer-links{position:absolute;left:144px;top:92px;font-size:11px;color:#bbb}
.footer-copy{position:absolute;left:144px;top:124px;font-size:11px;color:#bbb}
.social-dot{position:absolute;top:111px;width:18px;height:18px;border-radius:50%;background:#9a9a9a}
</style>
</head>
<body>

<header class="hero">
  <div class="hero-photo" role="img" aria-label="Aerial view of a winding river through dense Ecuadorian rainforest under a cloudy sky"></div>
  <div class="logo">Verdano</div>
  <nav class="nav">
    <span class="active">HOME</span><span>ABOUT US</span><span>SERVICES</span><span>NEWS</span><span>CONTACT US</span>
  </nav>
  <svg class="nav-search" width="14" height="14" viewBox="0 0 14 14"><circle cx="5.5" cy="5.5" r="4" fill="none" stroke="#fff" stroke-width="2"/><line x1="8.5" y1="8.5" x2="13" y2="13" stroke="#fff" stroke-width="2.4"/></svg>
  <div class="nav-btn" style="left:871px;width:96px">REGISTER</div>
  <div class="nav-btn" style="left:979px;width:76px">LOG IN</div>
  <h1 class="heading hero-title">Phasellus nisl est<br>condimentum vitae faucibus</h1>
  <div class="btn" style="left:528px;top:324px;width:143px;height:38px;font-size:16px">Get a quote</div>
  <div class="slider-arrow" style="left:54px"><svg width="14" height="20" viewBox="0 0 14 20"><polyline points="11,2 3,10 11,18" fill="none" stroke="#fff" stroke-width="3"/></svg></div>
  <div class="slider-arrow" style="left:1103px"><svg width="14" height="20" viewBox="0 0 14 20"><polyline points="3,2 11,10 3,18" fill="none" stroke="#fff" stroke-width="3"/></svg></div>
  <svg class="diag" style="bottom:0" height="60" viewBox="0 0 1200 60" preserveAspectRatio="none"><polygon points="0,60 1200,0 1200,60" fill="#f7941d"/><polygon points="0,60 1200,30 1200,60" fill="#fff"/></svg>
</header>

<section class="welcome">
  <h2 class="heading abs welcome-title">Welcome to Verdano</h2>
  <div class="accent-line" style="left:614px;top:746px;width:120px"></div>
  <div class="text-block welcome-block">
    <p class="body-copy">Quisque aliquet nec est vestibulum pulvinar. Pellentesque convallis molestie enim sit amet efficitur. Etiam id imperdiet lectus. Vivamus lacus justo, ultrices nec erat in, euismod iaculis mauris. Vivamus eleifend vitae nulla vel malesuada. In ac malesuada lacus, et consectetur ante. Fusce vitae lectus sit amet pulvinar maximus. Aenean placerat, nibh vel accumsan aliquet, magna nibh accumsan nibh, ac tempus nunc ipsum ac tellus.</p>
    <div class="btn inline" style="margin-top:20px;width:120px;height:40px">Read more</div>
  </div>
  <div class="photo-block" style="left:678px;top:726px;width:376px;height:288px;background:linear-gradient(180deg,#c9d7e6 0%,#b6c7d9 55%,#2f63a8 70%,#3f7fb8 100%)" role="img" aria-label="Container cargo ship at sea loaded with colourful containers"></div>
</section>

<section>
  <div class="products" role="img" aria-label="Dark dusk view of a cargo port with cranes and a ship"></div>
  <h2 class="heading products-title">Exporting products</h2>

  <div class="product-card" style="left:144px;top:1299px">
    <h3 class="heading">Flowers</h3>
    <p>Aenean feugiat viverra lorem ac sagittis. Donec sit amet lectus nec mi tempor laoreet ac nec nunc. Duis id auctor sapien.</p>
    <div class="product-photo" style="background:linear-gradient(135deg,#eadbe0,#c9b9cf 40%,#e8a9b3 70%,#f2e7e4)" role="img" aria-label="Bed of pastel roses in pink, white and lilac"></div>
  </div>
  <div class="card-stem" style="left:291px;top:1239px"></div>

  <div class="product-card" style="left:451px;top:1282px">
    <h3 class="heading">Chocolates</h3>
    <p>Aenean feugiat viverra lorem ac sagittis. Donec sit amet lectus nec mi tempor laoreet ac nec nunc. Duis id auctor sapien.</p>
    <div class="product-photo" style="background:linear-gradient(135deg,#6b4630,#4a2b1d 50%,#3a2218)" role="img" aria-label="Dark chocolate bar on cocoa powder"></div>
  </div>
  <div class="card-stem" style="left:598px;top:1223px"></div>

  <div class="product-card" style="left:757px;top:1299px">
    <h3 class="heading">Bananas</h3>
    <p>Aenean feugiat viverra lorem ac sagittis. Donec sit amet lectus nec mi tempor laoreet ac nec nunc. Duis id auctor sapien.</p>
    <div class="product-photo" style="background:linear-gradient(135deg,#f4c21b,#e6a70e 50%,#f6d23a)" role="img" aria-label="Bunches of ripe yellow bananas"></div>
  </div>
  <div class="card-stem" style="left:904px;top:1239px"></div>

  <svg class="diag" style="top:1708px" height="54" viewBox="0 0 1200 54" preserveAspectRatio="none"><polygon points="0,0 1200,54 0,28" fill="#f7941d"/><polygon points="0,28 1200,54 0,54" fill="#fff"/></svg>
</section>

<section class="why">
  <div class="photo-block" style="left:144px;top:1845px;width:376px;height:288px;background:linear-gradient(135deg,#8a6a4a,#d94aa0 40%,#b83a3a 65%,#7d8a52)" role="img" aria-label="Crates of colourful cut flowers at a flower market seen from above"></div>
  <div class="accent-line" style="left:520px;top:1866px;width:63px"></div>
  <h2 class="heading abs why-title">Why choose us</h2>
  <div class="text-block why-block">
    <p class="body-copy">Nam et tortor in ante iaculis porttitor in luctus mi. Vivamus gravida sem a pretium euismod. Nam lobortis, purus et fringilla tempus, risus eros dignissim diam, eget finibus sem risus sit amet eros. Vestibulum facilisis dolor at purus tincidunt porta. Nam fringilla nulla vel nisl condimentum, dapibus condimentum enim porta. Phasellus blandit quam a ipsum gravida dapibus. Suspendisse elit ligula, iaculis dignissim.</p>
    <div class="btn inline" style="margin-top:20px;width:120px;height:40px">Read more</div>
  </div>
</section>

<section>
  <div class="benefits" role="img" aria-label="Faded greyscale yard of stacked shipping containers"></div>

  <div class="benefit-label" style="left:0;width:1200px;text-align:center;top:2285px">Fresh &amp; Nature</div>
  <div class="benefit-label" style="right:844px;text-align:right;top:2437px">93% Organic<br>Products</div>
  <div class="benefit-label" style="left:845px;top:2452px">Perfect pakaging</div>
  <div class="benefit-label" style="right:844px;text-align:right;top:2598px">High Quality<br>Shipping Facility</div>
  <div class="benefit-label" style="left:842px;top:2628px">Resonable Pricing</div>
  <div class="benefit-label" style="left:0;width:1200px;text-align:center;top:2786px">Nutritional</div>

  <div class="benefit-circle" style="left:519px;top:2326px">
    <svg width="60" height="60" viewBox="0 0 60 60" fill="none" stroke="#1e1e1e" stroke-width="2.5"><path d="M30 6 C14 18 12 40 30 54 C48 40 46 18 30 6 Z"/><line x1="30" y1="14" x2="30" y2="56"/><line x1="30" y1="26" x2="21" y2="20"/><line x1="30" y1="26" x2="39" y2="20"/><line x1="30" y1="38" x2="19" y2="31"/><line x1="30" y1="38" x2="41" y2="31"/></svg>
  </div>
  <div class="benefit-circle" style="left:371px;top:2390px">
    <svg width="64" height="60" viewBox="0 0 64 60" fill="none" stroke="#1e1e1e" stroke-width="2.5"><path d="M4 40 h10 v16 h-10 z"/><path d="M14 44 h14 c4 0 6 4 2 6 h-10"/><path d="M14 52 h22 l18 -10 c3 -2 0 -6 -3 -5 l-13 6"/><path d="M34 34 c-8 0 -10 -4 -10 -8 h10 c6 0 8 4 8 8"/><line x1="34" y1="34" x2="34" y2="14"/><path d="M34 18 c0 -8 8 -12 16 -12 c0 8 -6 12 -16 12 z"/></svg>
  </div>
  <div class="benefit-circle" style="left:667px;top:2390px">
    <svg width="62" height="62" viewBox="0 0 62 62" fill="none" stroke="#1e1e1e" stroke-width="2.5"><path d="M8 18 L34 8 L56 18 L30 28 Z"/><path d="M8 18 V44 L30 56 V28"/><path d="M56 18 V44 L30 56"/><path d="M20 13 L44 23 V32"/><rect x="12" y="36" width="10" height="6"/></svg>
  </div>
  <h2 class="heading benefits-title">Benefits</h2>
  <div class="benefit-circle" style="left:371px;top:2555px">
    <svg width="64" height="60" viewBox="0 0 64 60" fill="none" stroke="#1e1e1e" stroke-width="2.5"><path d="M4 40 h56 l-8 14 h-40 z"/><path d="M14 40 v-12 h36 v12"/><path d="M22 28 v-10 h20 v10"/><line x1="32" y1="18" x2="32" y2="6"/><path d="M2 58 c6 -3 10 -3 16 0 c6 3 10 3 16 0 c6 -3 10 -3 16 0 c6 3 10 3 12 0"/></svg>
  </div>
  <div class="benefit-circle" style="left:667px;top:2555px">
    <svg width="64" height="64" viewBox="0 0 64 64" fill="none" stroke="#1e1e1e" stroke-width="2.5"><rect x="30" y="6" width="26" height="44"/><circle cx="43" cy="28" r="7"/><path d="M22 14 l8 -2 v40"/><path d="M4 38 h10 v22 h-10 z"/><path d="M14 42 h14 c6 0 6 10 0 10 h-14"/><path d="M28 48 h8"/></svg>
  </div>
  <div class="benefit-circle" style="left:519px;top:2620px">
    <svg width="66" height="60" viewBox="0 0 66 60" fill="none" stroke="#1e1e1e" stroke-width="2.5"><path d="M33 54 L10 32 C0 22 6 6 19 6 C26 6 31 11 33 15 C35 11 40 6 47 6 C60 6 66 22 56 32 Z"/><polyline points="4,30 20,30 26,20 32,40 38,24 42,30 62,30"/></svg>
  </div>

  <svg class="diag" style="top:2875px" height="48" viewBox="0 0 1200 48" preserveAspectRatio="none"><polygon points="0,48 1200,0 1200,48" fill="#f7941d"/><polygon points="0,48 1200,20 1200,48" fill="#fff"/></svg>
</section>

<section class="contact">
  <h2 class="heading contact-title">Contact us</h2>
  <div class="accent-line" style="left:540px;top:3063px;width:120px"></div>
  <div class="contact-line" style="top:3086px"><svg width="13" height="19" viewBox="0 0 13 19"><path d="M6.5 0 C2.9 0 0 2.9 0 6.5 C0 11 6.5 19 6.5 19 C6.5 19 13 11 13 6.5 C13 2.9 10.1 0 6.5 0 Z M6.5 9 A2.5 2.5 0 1 1 6.5 4 A2.5 2.5 0 1 1 6.5 9 Z" fill="#1e1e1e"/></svg>24 Building name, Street name, City Zipcode</div>
  <div class="contact-line" style="top:3126px"><svg width="17" height="17" viewBox="0 0 17 17"><path d="M3.5 0.5 L6.5 4 L4.8 6 C5.8 8.5 8.5 11.2 11 12.2 L13 10.5 L16.5 13.5 L14.5 16.5 C7 16 1 10 0.5 2.5 Z" fill="#1e1e1e"/></svg>555 014 2876 &nbsp;&nbsp;|&nbsp;&nbsp; <svg width="20" height="15" viewBox="0 0 20 15"><rect width="20" height="15" fill="#1e1e1e"/><polyline points="1,1 10,8 19,1" fill="none" stroke="#fff" stroke-width="1.5"/></svg>info@verdano.com</div>
  <div class="btn" style="left:528px;top:3175px;width:143px;height:38px;font-size:15px">Contact us</div>
</section>

<footer class="footer">
  <svg class="diag" style="top:-2px" height="60" viewBox="0 0 1200 60" preserveAspectRatio="none"><polygon points="0,0 1200,0 0,44" fill="#fff"/><polygon points="0,44 1200,0 1200,18 0,58" fill="#f7941d"/></svg>
  <div class="footer-links">Home &nbsp;&nbsp;|&nbsp;&nbsp; About Us &nbsp;&nbsp;|&nbsp;&nbsp; Services &nbsp;&nbsp;|&nbsp;&nbsp; News &nbsp;&nbsp;|&nbsp;&nbsp; Contact Us</div>
  <div class="footer-copy">Copyright &copy; 2020 &nbsp;Verdano. &nbsp;All rights reserved.</div>
  <div class="social-dot" style="left:991px"></div>
  <div class="social-dot" style="left:1034px"></div>
</footer>

</body>
</html>
```